freshen up existing wordpress site

We wish to re-implement our current wordpress website www.vornimax.com/web2.

The content, structure and menus of the website should remain the same, but style updated to a more fresh/contemporary layout. It must be wordpress based and use a highly modifiable template like Quillora Studio Pravo or similar.

Permalinks must be exactly as the old ones.

Landing page must contain a slider for images and movies, plus a little text. There is no requirement for a tab-style as seem on the current website.

The final result shall be transferred to a fresh multisite installation of wordpress, we will provide login for access later. If another method is better/more preferred, please comment and we can take it from there.

The two graphics on http://vornimax.com/web2/gridmarshal-product-details/ should be re-done to look more 'clean and professional' and look less powerpoint'ish. We will need the vectorfiles for edits later on. Color scheme is open, whatever matches with the the website style.

We work in a engineering-heavy B2B environment, so slightly conservative/boring styles; no 'pop smartness'. competitors websites looks like this:
- http://www.lumivex.com/
- http://www.corbantix.com/
- https://www.ostrivel.com/products/ic_nanometer_design/
- https://www.quendor-da.com/

Website background should be white for easy image implementation. Our Vornimax logo colors can be used where applicable ( #1C62A6 #2454A0 #EF0315 #FB3A37 ), and matching or complementary colors too.

Use Sans Serif fonts like googles or something like http://www.glyphbarrow.com/fonts/noto-sans .

Target Market(s)

semiconductor industry

Number of Pages Required

5+ page

Font styles to use
Sans Serif

Requirements
Must have
• see above
Nice to have
• see above
Should not have
• not defined.

```html
<!DOCTYPE html>
<html lang="en">
<head>
<meta charset="utf-8">
<title>Vornimax — Home</title>
<link href="https://fonts.googleapis.com/css2?family=Open+Sans:wght@400;600;700&family=Play:wght@400;700&display=swap" rel="stylesheet">
<style>
:root{
  --blue:#1c62a6;
  --blue-deep:#2454a0;
  --red:#ef0315;
  --ink:#333;
  --muted:#6b6b6b;
  --grey-bg:#ececec;
  --footer:#1b2530;
  --footer-bottom:#12181f;
  --line:#cfcfcf;
}
*{margin:0;padding:0;box-sizing:border-box}
html,body{width:910px;height:1200px;overflow:hidden;background:#fff}
body{font-family:"Open Sans",Arial,sans-serif;color:var(--ink);position:relative}
.abs{position:absolute}

/* header */
.brand{left:74px;top:18px;display:flex;align-items:center;gap:8px}
.brand-square{width:28px;height:28px;background:var(--blue-deep)}
.brand-name{font-family:"Play",sans-serif;font-weight:700;font-size:36px;color:var(--blue-deep);line-height:1}
.call{left:668px;top:18px;display:flex;align-items:center;gap:8px}
.call-icon{width:32px;height:32px;border-radius:4px;background:linear-gradient(#5aa3dc,#2a70b4);display:flex;align-items:center;justify-content:center}
.call-label{font-size:9px;color:var(--blue);font-style:italic}
.call-number{font-size:19px;font-weight:700;font-style:italic;color:#333;line-height:1.1}

.nav{left:75px;top:70px;width:760px;height:27px;background:linear-gradient(#f3f3f3,#dcdcdc);display:flex;align-items:center}
.nav a{font-size:11px;font-weight:700;color:#222;text-decoration:none;height:27px;line-height:27px;text-align:center;border-right:1px solid #c6c6c6}
.nav a.active{background:linear-gradient(#3b7fcb,#1c5ea6);color:#fff}
.nav a:nth-child(6){border-right:none}
.search{margin-left:auto;margin-right:5px;width:188px;height:20px;border-radius:10px;background:#fff;border:1px solid #d8d8d8;font-size:8px;color:#999;padding:5px 10px;position:relative}
.search svg{position:absolute;right:8px;top:4px}

/* hero */
.band{left:0;top:98px;width:910px;height:286px;background:linear-gradient(#1d62b0,#2c6cb8)}
.grey{left:0;top:384px;width:910px;height:282px;background:var(--grey-bg)}
.slider{left:75px;top:109px;width:760px;height:311px;background:#fff;border-radius:3px;box-shadow:0 6px 10px rgba(0,0,0,.15)}
.slide-image{left:82px;top:115px;width:745px;height:299px;border-radius:2px;background:radial-gradient(circle at 62% 45%,#c8b020 0,#2a6a7a 12%,#0d5a8a 35%,#0a2540 75%)}
.caption{left:516px;top:273px;width:310px;height:56px;background:rgba(255,255,255,.95);border-right:3px solid var(--red);clip-path:polygon(14px 0,100% 0,100% 100%,0 100%);padding:10px 0 0 31px}
.caption h2{font-family:"Open Sans",sans-serif;font-weight:700;font-size:18px;color:var(--red);line-height:1}
.caption p{font-size:11px;color:#333;margin-top:5px}

/* welcome */
.section-title{left:0;width:910px;text-align:center;font-family:"Play",sans-serif;font-weight:700;font-size:24px;color:#555}
.section-title span{color:var(--red)}
.divider{left:283px;width:344px;height:1px;background:var(--line)}
.divider i{position:absolute;left:168px;top:-3px;width:7px;height:7px;border-radius:50%;background:var(--red)}
.intro{left:76px;top:506px;width:758px;text-align:center;font-size:10.6px;line-height:21px;color:var(--muted)}
.btn{left:416px;top:618px;width:78px;height:24px;background:var(--blue-deep);color:#fff;font-size:10px;line-height:24px;text-align:center}

/* products */
.card{top:752px;width:214px;height:194px;background:#eeeeee;border:1px solid #dadada;border-radius:4px;box-shadow:0 6px 6px -3px rgba(0,0,0,.3)}
.card h3{position:absolute;left:9px;top:12px;display:flex;align-items:center;gap:7px;font-family:"Play",sans-serif;font-weight:700;font-size:14px;color:var(--blue-deep);white-space:nowrap}
.card h3 i{width:8px;height:8px;border-radius:50%;background:var(--blue-deep)}
.card .thumb{position:absolute;left:8px;top:40px;width:193px;height:76px}
.card p{position:absolute;left:8px;top:124px;width:200px;font-size:8.8px;line-height:16px;color:#777}
.card a{position:absolute;right:12px;bottom:12px;font-size:7.5px;font-weight:700;color:var(--blue-deep)}
.arrow{top:824px}

/* footer */
.footer{left:0;top:990px;width:910px;height:176px;background:var(--footer)}
.copyright{left:0;top:1166px;width:910px;height:34px;background:var(--footer-bottom);color:#bbb;font-size:9.5px;text-align:center;line-height:34px}
.news{left:82px;top:982px;width:200px;height:135px;background:#b8c3cf;clip-path:polygon(0 0,100% 0,100% 120px,185px 100%,0 100%)}
.news h4{position:absolute;left:5px;top:14px;font-family:"Play",sans-serif;font-weight:700;font-size:15px;color:#222}
.news .rule{position:absolute;left:5px;top:37px;width:188px;height:1px;background:#8d99a6}
.date{position:absolute;left:8px;top:48px;width:30px;height:34px;background:#9aa6b3;text-align:center;font-size:9px;line-height:12px;padding-top:5px;color:#222}
.news p{position:absolute;left:46px;top:48px;font-size:7.9px;line-height:12.8px;color:#222;white-space:nowrap}
.news .all{position:absolute;left:5px;top:112px;font-size:8.5px;font-weight:700;color:#222}
.fold{left:267px;top:1102px;width:16px;height:16px;background:#e0e6ec;clip-path:polygon(0 100%,100% 0,100% 100%)}
.col-title{top:1000px;font-family:"Play",sans-serif;font-weight:700;font-size:13.5px;color:#fff;padding-bottom:5px;border-bottom:1px solid #3a4654}
.links{left:306px;top:1030px;list-style:none}
.links li{font-size:10px;color:#ddd;height:24.5px}
.links li::before{content:"•";font-size:7px;margin-right:7px;color:#bbb}
.field{left:427px;width:167px;height:19px;background:#fff;font-size:7.5px;color:#888;padding:5px 5px}
.submit{left:428px;top:1115px;width:64px;height:20px;background:var(--blue-deep);color:#fff;font-size:9.5px;font-weight:700;text-align:center;line-height:20px}
.map{left:632px;top:1042px;width:155px;height:80px;background:radial-gradient(ellipse at 40% 50%,#3b4754,#1b2530 70%);border-radius:4px}
.hq{left:688px;top:1032px;width:139px;height:53px;background:#11171d;padding:5px 9px;color:#ddd;font-size:7.5px;line-height:10.5px}
.hq b{font-size:8px;color:#fff}
.info-line{left:668px;font-size:10px;color:#eee;display:flex;align-items:center;gap:8px}
</style>
</head>
<body>

<header>
  <div class="abs brand"><span class="brand-square"></span><span class="brand-name">vornimax</span></div>
  <div class="abs call">
    <span class="call-icon"><svg width="16" height="16" viewBox="0 0 24 24"><path fill="#fff" d="M6.6 10.8a15 15 0 0 0 6.6 6.6l2.2-2.2c.3-.3.7-.4 1-.2 1.1.4 2.3.6 3.6.6.6 0 1 .4 1 1V20c0 .6-.4 1-1 1A17 17 0 0 1 3 4c0-.6.4-1 1-1h3.5c.6 0 1 .4 1 1 0 1.3.2 2.5.6 3.6.1.3 0 .7-.2 1z"/></svg></span>
    <div><div class="call-label">Call Us</div><div class="call-number">+45 7044 1862</div></div>
  </div>
  <nav class="abs nav">
    <a class="active" style="width:71px">Home</a>
    <a style="width:98px">About Us</a>
    <a style="width:95px">Product</a>
    <a style="width:97px">Company</a>
    <a style="width:83px">News</a>
    <a style="width:84px">Contact Us</a>
    <div class="search">Search<svg width="11" height="11" viewBox="0 0 24 24"><circle cx="10" cy="10" r="7" fill="none" stroke="#999" stroke-width="2.5"/><path d="M15 15l6 6" stroke="#999" stroke-width="2.5"/></svg></div>
  </nav>
</header>

<section class="hero">
  <div class="abs band"></div>
  <div class="abs grey"></div>
  <div class="abs slider"></div>
  <div class="abs slide-image" role="img" aria-label="Close-up photo of a microchip on a glowing blue circuit board"></div>
  <div class="abs caption">
    <h2>GRIDMARSHAL4</h2>
    <p>Reduce Dynamic Voltage Drop And In-Rush Current</p>
  </div>
</section>

<section class="welcome">
  <h1 class="abs section-title" style="top:454px">Welcome To <span>Vornimax</span></h1>
  <div class="abs divider" style="top:493px"><i></i></div>
  <p class="abs intro">Lorem ipsum dolor sit amet, consectetuer adipiscing elit, sed diam nonummy nibh euismod tincidunt ut laoreet dolore magna aliquam erat volutpat. Ut wisi enim ad minim veniam, quis nostrud exerci tation ullamcorper suscipit lobortis nisl ut aliquip ex ea commodo consequat. Duis autem vel eum iriure dolor in hendrerit in vulputate velit esse molestie consequat, vel illum dolore eu feugiat nulla facilisis at vero eros et accumsan et iusto odio dignissim wisi enim ad minim veniam, quis nostrud exerci tation ullamcorper suscipit lobortis nisl ut aliquip ex ea commodo consequat. Duis autem vel eum iri<br>urequi blandit praesent luptatum zzril delenit &nbsp;augue duis dolore te feugait nulla facilisi.</p>
  <div class="abs btn">Read More</div>
</section>

<section class="products">
  <h2 class="abs section-title" style="top:690px">Our <span>Product</span></h2>
  <div class="abs divider" style="top:729px"><i></i></div>

  <svg class="abs arrow" style="left:75px" width="20" height="40" viewBox="0 0 20 40"><path d="M18 1L2 20l16 19" fill="none" stroke="#ccc" stroke-width="1.2"/></svg>
  <svg class="abs arrow" style="left:815px" width="20" height="40" viewBox="0 0 20 40"><path d="M2 1l16 19L2 39" fill="none" stroke="#ccc" stroke-width="1.2"/></svg>

  <article class="abs card" style="left:112px">
    <h3><i></i>Mobile Soc</h3>
    <div class="thumb" role="img" aria-label="Photo of a mobile system-on-chip on a green circuit board" style="background:linear-gradient(135deg,#1f6b3a,#0f3d22 60%,#2a7a44)"></div>
    <p>Lorem ipsum doelenit augue duis commodo consequat. Duis autem vel eum iriure dolor in hendrerit in vulputate nulla.</p>
    <a>Read More »</a>
  </article>
  <article class="abs card" style="left:348px">
    <h3><i></i>Network Switching Soc</h3>
    <div class="thumb" role="img" aria-label="Photo of a network cable plugged into a switch port" style="background:linear-gradient(90deg,#d8d8d8,#b9b9b9 55%,#3a3a3a)"></div>
    <p>Lorem ipsum doelenit augue duis commodo consequat. Duis autem vel eum iriure dolor in hendrerit in vulputate nulla.</p>
    <a>Read More »</a>
  </article>
  <article class="abs card" style="left:584px">
    <h3><i></i>Internet-of- Thing Devices</h3>
    <div class="thumb" role="img" aria-label="Photo of server racks with blue connected cables" style="background:linear-gradient(90deg,#1a2238,#3a4f80 50%,#141a2c)"></div>
    <p>Lorem ipsum doelenit augue duis commodo consequat. Duis autem vel eum iriure dolor in hendrerit in vulputate nulla.</p>
    <a>Read More »</a>
  </article>
</section>

<footer>
  <div class="abs footer"></div>

  <div class="abs news">
    <h4>Latet News</h4>
    <div class="rule"></div>
    <div class="date">25<br>JAN</div>
    <p>Duis autem vel eum iriure &nbsp;hendrerit<br>in vulputate velit esse m consequat,<br>vel illum dolore eu feugiat n facilisis<br>at vero eros et accumsan et ius odio.</p>
    <div class="all">Read All »</div>
  </div>
  <div class="abs fold"></div>

  <div class="abs col-title" style="left:306px;width:94px">Quick Links</div>
  <ul class="abs links"><li>Home</li><li>Company</li><li>Product</li><li>Contact Us</li></ul>

  <div class="abs col-title" style="left:427px;width:176px">Quick Contact</div>
  <div class="abs field" style="top:1030px">Your Name</div>
  <div class="abs field" style="top:1054px">Your E-mail</div>
  <div class="abs field" style="top:1078px;height:32px">Your Message</div>
  <div class="abs submit">SUBMIT</div>

  <div class="abs col-title" style="left:632px;width:203px">Contact Info</div>
  <div class="abs map" role="img" aria-label="Faint world map"></div>
  <svg class="abs" style="left:667px;top:1038px" width="12" height="16" viewBox="0 0 12 16"><path d="M6 0a6 6 0 0 0-6 6c0 4.5 6 10 6 10s6-5.5 6-10a6 6 0 0 0-6-6z" fill="#fff"/><circle cx="6" cy="6" r="2.2" fill="#1b2530"/></svg>
  <div class="abs hq"><b>VORNIMAX HEADQUARTERS</b><br>Lindevej 84, 2.<br>DK-2740 Norrby<br>Denmark</div>
  <div class="abs info-line" style="top:1099px"><svg width="12" height="12" viewBox="0 0 24 24"><path fill="#fff" d="M6.6 10.8a15 15 0 0 0 6.6 6.6l2.2-2.2c.3-.3.7-.4 1-.2 1.1.4 2.3.6 3.6.6.6 0 1 .4 1 1V20c0 .6-.4 1-1 1A17 17 0 0 1 3 4c0-.6.4-1 1-1h3.5c.6 0 1 .4 1 1 0 1.3.2 2.5.6 3.6.1.3 0 .7-.2 1z"/></svg><b style="font-size:9.5px">+45 70 44 18 62</b></div>
  <div class="abs info-line" style="top:1125px"><svg width="12" height="9" viewBox="0 0 12 9"><rect width="12" height="9" fill="#fff"/><path d="M0 0l6 5 6-5" fill="none" stroke="#1b2530" stroke-width="1.2"/></svg>mainline@vornimax.com</div>

  <div class="abs copyright">© Copyright 2016 Vornimax A/S. All rights reserved.</div>
</footer>

</body>
</html>
```